Kelvaro.ch is looking for business card letterhead and envelope C5 with WOW effect

We need a strong business card for our company Kelvaro.ch, logo is available. You want a black or dark background on which the logo Stark r% 26 # 252; appears. Letterhead and envelope in C5 format should be in a similar design, but does not have to be We need a strong business card for our company Kelvaro.ch, logo is available. A black or dark background is desired, on which the logo Stark comes across. The letterhead and the envelope in C5 format should have a similar design.

Target Market(s)

Private customers as well as entrepreneurs

Contact Information for Business Card

E-mail: info@kelvaro-example.ch
Web.www.Kelvaro-example.ch
Tel: +41 ( 0 ) 79 482 6037
Adresse:
Lindenweg 14
9406 Tarnbach

Hier kann man Icons verwenden für Email,Tel und Adressse

Font styles to use
Other font styles liked:
• Dubai,bold

Colors

Designer to choose colors to be used in the design.

Requirements
Must have
• WOW effect
Nice to have
• R% 26 # 252; back business card with our service listings. - VEHICLE LABELING - SHOP WINDOW LABELING - STICKERS AND MUCH MORE ... in red color

```html
<!DOCTYPE html>
<html lang="en">
<head>
<meta charset="utf-8">
<title>Kelvaro.ch – Business Card</title>
<link rel="stylesheet" href="https://fonts.googleapis.com/css2?family=Nunito:wght@400;800&family=Russo+One&display=swap">
<style>
  :root {
    --stage: #262626;
    --card: #0b0b0b;
    --accent: #fcc71e;
    --ink: #ffffff;
    --ink-dark: #0b0b0b;
    --muted: #d8d8d8;
  }
  * { box-sizing: border-box; margin: 0; padding: 0; }
  html, body { width: 1200px; height: 900px; overflow: hidden; }
  body {
    background: radial-gradient(circle at 50% 35%, #333 0%, var(--stage) 70%);
    font-family: "Nunito", sans-serif;
    color: var(--ink);
    position: relative;
  }
  .card {
    position: absolute;
    left: 250px;
    width: 700px;
    height: 400px;
    background: var(--card);
    box-shadow: 0 18px 40px rgba(0,0,0,.55);
    overflow: hidden;
  }
  .card--front { top: 38px; border-right: 4px solid var(--accent); }
  .card--back  { top: 462px; border-left: 4px solid var(--accent); }

  .front-pattern {
    position: absolute;
    left: 0; top: 0;
    width: 320px; height: 400px;
    background: radial-gradient(ellipse at 45% 50%, var(--accent) 0%, #d9a80f 38%, rgba(11,11,11,0) 72%);
  }
  .front-texture {
    position: absolute;
    right: 0; top: 0;
    width: 380px; height: 400px;
    background: radial-gradient(ellipse at 60% 55%, #1c1c1c 0%, rgba(11,11,11,0) 70%);
  }
  .front-name {
    position: absolute;
    left: 340px; top: 160px;
    font-weight: 800;
    font-size: 62px;
    letter-spacing: 1px;
    color: var(--ink);
  }

  .logo-panel {
    position: absolute;
    left: 150px; top: 28px;
    width: 410px; height: 160px;
    background: var(--accent);
    display: flex; align-items: center; justify-content: center;
  }
  .logo-panel__name {
    font-weight: 800;
    font-size: 62px;
    color: var(--ink-dark);
  }

  .holder {
    position: absolute;
    right: 420px; top: 275px;
    text-align: right;
  }
  .holder__name {
    font-family: "Russo One", sans-serif;
    font-size: 34px;
    color: var(--accent);
    text-transform: uppercase;
    letter-spacing: 1px;
    line-height: 1.05;
  }
  .holder__role { font-size: 20px; color: var(--ink); }

  .divider {
    position: absolute;
    left: 300px; top: 270px;
    width: 2px; height: 100px;
    background: var(--accent);
  }

  .contacts {
    position: absolute;
    left: 322px; top: 268px;
    list-style: none;
    font-size: 17px;
    line-height: 26px;
    color: var(--ink);
  }
  .contacts li { display: flex; align-items: center; gap: 10px; }
  .contacts svg { width: 18px; height: 18px; flex: none; }
  .contacts .highlight { color: var(--accent); font-weight: 800; }
</style>
</head>
<body>

<section class="card card--front">
  <div class="front-pattern" role="img" aria-label="Cluster of yellow honeycomb hexagons"></div>
  <div class="front-texture" role="img" aria-label="Faint dark honeycomb texture"></div>
  <div class="front-name">Kelvaro.ch</div>
</section>

<section class="card card--back">
  <div class="logo-panel"><span class="logo-panel__name">Kelvaro.ch</span></div>

  <div class="holder">
    <div class="holder__name">Dario Venn</div>
    <div class="holder__role">Owner/ CEO</div>
  </div>

  <div class="divider"></div>

  <ul class="contacts">
    <li>
      <svg viewBox="0 0 24 24" fill="none" stroke="var(--accent)" stroke-width="2"><circle cx="12" cy="12" r="10"/><path d="M8 7c0 5 4 9 9 9l1-2-3-1-1 1c-2-1-3-2-4-4l1-1-1-3z"/></svg>
      +41 ( 0 ) 79 482 6037
    </li>
    <li>
      <svg viewBox="0 0 24 24" fill="none" stroke="var(--accent)" stroke-width="2"><rect x="2" y="5" width="20" height="14"/><path d="M2 5l10 8 10-8"/></svg>
      info@kelvaro-example.ch
    </li>
    <li>
      <svg viewBox="0 0 24 24" fill="none" stroke="var(--accent)" stroke-width="2"><circle cx="12" cy="12" r="10"/><path d="M2 12h20M12 2c3 3 3 17 0 20M12 2c-3 3-3 17 0 20"/></svg>
      <span>www.<span class="highlight">Kelvaro-example</span>.ch</span>
    </li>
    <li>
      <svg viewBox="0 0 24 24" fill="none" stroke="var(--accent)" stroke-width="2"><path d="M3 11l9-8 9 8v10H3z"/><path d="M10 21v-6h4v6"/></svg>
      Lindenweg 14, 9406 Tarnbach
    </li>
  </ul>
</section>

</body>
</html>
```